I need a business card designed using the logo provided either vertical or horizontal......Harbourline Property Group is an Australian based real estate company that caters for the upper end of the market so the design of the business card "must reflect" the companies image!!
Colour combinations are optional but "must be realistic" and must be able to be accurately useable CMYK colours.
Please consider that any colours used "must be able to be used" and be suitable in following designs for "pull out banner signs" and "real estate signs".
The colours and the font in the attached designs are for example and other combinations are encouraged.
Target Market(s)
The High End of the Australian real estate market
Industry/Entity Type
Business
Contact Information for Business Card
Logo - Business Name - Director + Licensed Real Estate Agent - Mobile Number (Cell Phone) - Business Number - Fax - Email Address - Web address
Requirements
Must have
- Designs and colours (CMYK) that can easily be interpreted by an Australian printer.
Nice to have
- Some alternative ideas on colour and font..........the ones provided are ok and have been provided as an example but I am looking for alternative ideas
Should not have
- Loud, overly bright colours. Designs that do not reflect the professional standards of the business.
- Designs that look good on a computer monitor but can not be re-created on a printing press.............this is most important when it comes to shading etc.

```html
<!DOCTYPE html>
<html lang="en">
<head>
<meta charset="UTF-8">
<title>Harbourline Property Group — Business Card</title>
<link rel="stylesheet" href="https://fonts.googleapis.com/css2?family=Montserrat:wght@400;500;700&display=swap">
<style>
  :root {
    --bg: #e4e4e4;
    --card-white: #ffffff;
    --card-black: #0d0d0d;
    --ink: #1b1b1b;
    --ink-soft: #3a3a3a;
    --gold: #c8963e;
    --gold-light: #e0c48a;
    --card-w: 540px;
    --card-h: 310px;
  }
  * { box-sizing: border-box; margin: 0; padding: 0; }
  html, body {
    width: 1200px; height: 852px; overflow: hidden;
    background: var(--bg);
    font-family: "Montserrat", Arial, sans-serif;
  }
  .stage {
    width: 1200px; height: 852px;
    display: flex; align-items: center; justify-content: center; gap: 40px;
  }
  .card {
    position: relative;
    width: var(--card-w); height: var(--card-h);
    border-radius: 18px;
    overflow: hidden;
    background: var(--card-white);
    box-shadow: 0 2px 6px rgba(0,0,0,.12);
  }
  /* Front */
  .card-front {
    display: flex; align-items: center; justify-content: center; gap: 12px;
  }
  .brand-mark {
    width: 14px; height: 14px; background: var(--gold); flex: none;
  }
  .brand-name {
    font-weight: 700; font-size: 26px; letter-spacing: .04em;
    text-transform: uppercase; color: var(--ink); line-height: 1.15;
    text-align: left;
  }
  /* Back */
  .card-back .panel {
    position: absolute; inset: 0; width: 100%; height: 100%;
  }
  .back-brand {
    position: absolute; left: 0; top: 0; width: 250px; height: 100%;
    display: flex; align-items: center; justify-content: center; gap: 10px;
    padding-left: 18px;
  }
  .back-brand .brand-name { color: #ffffff; font-size: 18px; }
  .contact {
    position: absolute; left: 300px; top: 44px; right: 24px;
    color: var(--ink);
  }
  .person-name {
    font-weight: 700; font-size: 15px; letter-spacing: .06em;
  }
  .person-role {
    font-size: 10.5px; color: var(--ink-soft); margin-top: 3px;
  }
  .address {
    font-size: 10.5px; line-height: 1.45; color: var(--ink-soft);
    margin-top: 48px;
  }
  .contact-list { list-style: none; margin-top: 10px; }
  .contact-list li {
    display: flex; align-items: center; gap: 9px;
    font-size: 10.5px; line-height: 1.9; color: var(--ink-soft);
  }
  .contact-list svg { width: 11px; height: 11px; flex: none; }
</style>
</head>
<body>
<main class="stage">

  <section class="card card-front" aria-label="Business card front">
    <span class="brand-mark"></span>
    <span class="brand-name">Harbourline<br>Property Group</span>
  </section>

  <section class="card card-back" aria-label="Business card back">
    <svg class="panel" viewBox="0 0 540 310" preserveAspectRatio="none" aria-hidden="true">
      <defs>
        <linearGradient id="goldEdge" x1="0" y1="0" x2="0" y2="1">
          <stop offset="0" stop-color="#e0c48a"/>
          <stop offset="1" stop-color="#b07c2c"/>
        </linearGradient>
      </defs>
      <path d="M0 60 C70 40 160 30 215 55 C265 80 240 170 262 230 C275 270 285 295 290 310 L0 310 Z" fill="url(#goldEdge)"/>
      <path d="M0 64 C70 46 155 38 206 60 C252 84 228 172 250 232 C262 270 272 295 277 310 L0 310 Z" fill="#0d0d0d"/>
    </svg>

    <div class="back-brand">
      <span class="brand-mark"></span>
      <span class="brand-name">Harbourline<br>Property Group</span>
    </div>

    <div class="contact">
      <p class="person-name">YOUR LONG NAME</p>
      <p class="person-role">Managing Director</p>
      <p class="address">Your Commercial or office<br>address in just two line</p>
      <ul class="contact-list">
        <li>
          <svg viewBox="0 0 12 12"><path d="M2 1h2.5l1 3-1.5 1a6 6 0 0 0 3 3l1-1.5 3 1V10a1 1 0 0 1-1 1A9 9 0 0 1 1 2a1 1 0 0 1 1-1z" fill="#c8963e"/></svg>
          00.00.00.0000
        </li>
        <li>
          <svg viewBox="0 0 12 12"><rect x="3" y="0.5" width="6" height="11" rx="1" fill="#c8963e"/><rect x="4" y="2" width="4" height="7" fill="#fff"/></svg>
          00.00.00.0000
        </li>
        <li>
          <svg viewBox="0 0 12 12"><rect x="0.5" y="2" width="11" height="8" fill="#c8963e"/><path d="M0.5 2 6 7 11.5 2" fill="none" stroke="#fff" stroke-width="1"/></svg>
          yourname@yourwebsite.com
        </li>
        <li>
          <svg viewBox="0 0 12 12"><circle cx="6" cy="6" r="5.5" fill="#c8963e"/><path d="M0.5 6h11M6 0.5c-2.5 3-2.5 8 0 11M6 0.5c2.5 3 2.5 8 0 11" fill="none" stroke="#fff" stroke-width=".8"/></svg>
          www.yourwebsite.com
        </li>
      </ul>
    </div>
  </section>

</main>
</body>
</html>
```